Private Investment Firm Needs PowerPoint Presentation Template

Design PowerPoint template, take Pinebrook-submitted rough presentation draft, and drop it into new template. See attached Project Brief file for more detail.
Updates

Some decent designs have been submitted but they seem to lack the understanding of our target markets. I am hopeful that more time and feedback will result in better results.

Target Market(s)

Private company owners and intermediaries.

Font styles to use
Serif

Colors
3176b5

Requirements
Must have
• See attached Project Brief.
Nice to have
Should not have
• No B2C fluff--this is a B2B project.

```html
<!DOCTYPE html>
<html lang="en">
<head>
<meta charset="utf-8">
<title>Pinebrook Capital – Presentation Template</title>
<link href="https://fonts.googleapis.com/css2?family=Montserrat:wght@400;500;600;700;800&display=swap" rel="stylesheet">
<style>
  :root{
    --brand-blue:#1b74bb;
    --accent-blue:#3176b5;
    --navy:#264a6b;
    --teal:#1a9a87;
    --text:#555b61;
    --section-bg:#f0f0f0;
    --row-dark:#5f5f5f;
    --row-mid:#a3a3a3;
    --row-light:#cfcfcf;
  }
  *{box-sizing:border-box;margin:0;padding:0}
  html,body{width:1200px;height:1200px;overflow:hidden;background:#fff}
  body{font-family:"Montserrat",Arial,sans-serif;color:var(--text)}
  .deck{display:grid;grid-template-columns:repeat(3,397px);grid-template-rows:repeat(3,397px);gap:4px;width:1200px;height:1200px}
  .slide{position:relative;overflow:hidden;background:#fff;border:1px solid #e3e3e3}
  .slide--section{background:var(--section-bg);border:none;display:flex;align-items:center;justify-content:center;text-align:center}
  .section-title{color:var(--brand-blue);font-weight:700;font-size:27px;line-height:1.22;padding:0 20px}

  .top-bar{position:absolute;top:0;left:40px;right:0;height:24px;background:var(--navy)}
  .top-bar::before{content:"";position:absolute;left:0;top:0;width:26px;height:24px;background:var(--accent-blue);clip-path:polygon(0 0,60% 0,100% 100%,45% 100%)}
  .bottom-bar{position:absolute;bottom:0;left:0;width:272px;height:24px;background:var(--navy);clip-path:polygon(0 0,88% 0,100% 100%,0 100%);color:#fff;font-weight:700;font-size:10px;display:flex;align-items:center;justify-content:center;padding-left:18px}
  .bottom-accent{position:absolute;bottom:0;left:258px;width:38px;height:24px;background:var(--accent-blue);clip-path:polygon(0 0,30% 0,100% 100%,62% 100%)}
  .footer-brand{position:absolute;right:12px;bottom:4px;display:flex;align-items:center;gap:4px}
  .footer-brand .dot{width:13px;height:13px;border-radius:50%;background:var(--accent-blue)}
  .footer-brand .name{font-weight:600;font-size:9.5px;letter-spacing:.8px;color:var(--navy);line-height:1}
  .footer-brand .tag{font-size:3.6px;color:var(--navy);letter-spacing:.3px;display:block;margin-top:2px}

  .slide-title{position:absolute;left:8px;right:8px;color:var(--brand-blue);font-weight:700;font-size:21.5px;line-height:1.02;text-align:center}
  .bullets{position:absolute;list-style:none}
  .bullets li{position:relative;padding-left:13px;font-size:11.3px;font-weight:500;color:var(--text);line-height:1.22}
  .bullets li::before{content:"";position:absolute;left:1px;top:3.5px;width:5px;height:7px;border-radius:3px;border:1.5px solid #7b9ec0}
  .bullets .sub{display:block;font-size:8.4px;font-weight:400;line-height:2.1;margin-left:-13px;padding-left:14px}

  .case{position:absolute;left:38px;width:324px;display:flex;border:2px solid var(--teal)}
  .case-label{width:124px;background:#fff;text-align:center;padding-top:12px;color:var(--brand-blue);font-weight:600;font-size:10.5px;line-height:1.28}
  .case-label .company{display:block;margin-top:30px;font-weight:700;font-size:12px}
  .case-body{flex:1;background:var(--teal);color:#fff;padding:8px 6px 6px 10px}
  .case-body ul{list-style:disc;padding-left:8px}
  .case-body li{font-size:5.8px;line-height:1.35;margin-bottom:6px}
  .case-2 .case-body li{font-size:6.6px;margin-bottom:9px}

  .impact-table{position:absolute;left:20px;top:142px;width:360px;border-collapse:separate;border-spacing:3px 0;text-align:center}
  .impact-table th{background:var(--teal);color:#fff;font-weight:700;font-size:12.5px;height:55px;line-height:1.35}
  .impact-table td{font-weight:700;font-size:10.5px;color:#111;line-height:1.6}
  .impact-table td:first-child{font-size:10.8px}
  .row-1 td{background:var(--row-dark);color:#fff;height:54px}
  .row-2 td{background:var(--row-mid);height:40px}
  .row-3 td{background:var(--row-light);height:46px}
</style>
</head>
<body>
<main class="deck">

  <section class="slide">
    <div class="top-bar"></div>
    <h2 class="slide-title" style="top:58px">Pinebrook Representative<br>Non-Control Capital Investments</h2>
    <div class="case case-1" style="top:130px;height:112px">
      <div class="case-label">Family Ownership &amp;<br>Wealth Transfer<span class="company" style="color:#c8202e">Summit Signal</span></div>
      <div class="case-body"><ul>
        <li>Provider of fire and security alarm design, installation, service, and monitoring work for commercial and residential end-markets.</li>
        <li>Pinebrook's capital gave the founder room to think strategically, focus on growth and build family wealth. Five years later the company bought out Pinebrook's position with senior debt, and the son and key managers came to own the business outright while the father worked through his estate plans.</li>
      </ul></div>
    </div>
    <div class="case case-2" style="top:244px;height:112px">
      <div class="case-label">Family Office<br>Support<span class="company" style="color:#111">Orbis Packaging</span></div>
      <div class="case-body" style="padding-top:14px"><ul>
        <li>Provides comprehensive and custom packaging for the liquid home cleaning products sector, and has the ability to safely process volatile liquids, such as bleach and hydrogen peroxide.</li>
        <li>Pinebrook's capital was used to assist a New York-based family office in acquiring the Company as part of their business outsourcing growth strategy thesis.</li>
      </ul></div>
    </div>
    <div class="bottom-bar">15</div><div class="bottom-accent"></div>
    <div class="footer-brand"><span class="dot"></span><span class="name">PINEBROOK<span class="tag">NON-CONTROL GROWTH CAPITAL</span></span></div>
  </section>

  <section class="slide slide--section"><h2 class="section-title">Investment Criteria</h2></section>

  <section class="slide">
    <div class="top-bar"></div>
    <h2 class="slide-title" style="top:48px">Pinebrook Invests In Established, Lower Middle Market Companies.</h2>
    <ul class="bullets" style="left:14px;right:10px;top:116px">
      <li style="margin-bottom:13px">Revenues of $10MM to $150MM</li>
      <li style="margin-bottom:13px">EBITDA of at least $2MM</li>
      <li style="margin-bottom:13px">Pinebrook investment size of $5MM to $25MM</li>
      <li style="margin-bottom:13px">Experienced, committed, and incented management</li>
      <li style="margin-bottom:13px">Limited leverage (aka debt) “ahead” of Pinebrook</li>
      <li style="margin-bottom:13px">Niche market leader with differentiated services or products</li>
      <li>Focused on value-added execution, not proof of concept</li>
    </ul>
    <div class="bottom-bar">16</div><div class="bottom-accent"></div>
    <div class="footer-brand"><span class="dot"></span><span class="name">PINEBROOK<span class="tag">NON-CONTROL GROWTH CAPITAL</span></span></div>
  </section>

  <section class="slide slide--section"><h2 class="section-title">Consultants With Capital</h2></section>

  <section class="slide">
    <div class="top-bar"></div>
    <h2 class="slide-title" style="top:56px">We Help Portfolio Companies Create Greater Value.</h2>
    <ul class="bullets" style="left:14px;right:4px;top:117px">
      <li style="margin-bottom:12px">Facilitate strategy development</li>
      <li style="margin-bottom:12px">Improve financial reporting and information systems</li>
      <li style="margin-bottom:12px">Assist with key hires, such as CFOs and COOs, if needed</li>
      <li style="margin-bottom:12px">Source, evaluate, finance, close, and integrate acquisitions</li>
      <li style="margin-bottom:12px">Invest additional capital</li>
      <li style="margin-bottom:12px">Annual Executive Summit focused on professional development and networking</li>
      <li style="margin-bottom:12px">Most importantly, act as a sounding board to help solve problems, identify new opportunities, and create value</li>
      <li>We personally invest in every transaction</li>
    </ul>
    <div class="bottom-bar">17</div><div class="bottom-accent"></div>
    <div class="footer-brand"><span class="dot"></span><span class="name">PINEBROOK<span class="tag">NON-CONTROL GROWTH CAPITAL</span></span></div>
  </section>

  <section class="slide slide--section"><h2 class="section-title">Pinebrook Impact - By<br>The Numbers</h2></section>

  <section class="slide">
    <div class="top-bar"></div>
    <h2 class="slide-title" style="top:52px">During Pinebrook's Average Investment Term, Our Impact Has Been Noteworthy</h2>
    <table class="impact-table">
      <thead><tr><th>Impact Category</th><th>Actual Impact</th><th>Min/Max*<br>Removed</th></tr></thead>
      <tbody>
        <tr class="row-1"><td>Average Revenue<br>Growth</td><td>113%</td><td>91%</td></tr>
        <tr class="row-2"><td>Average EBITDA<br>Growth</td><td>75%</td><td>78%</td></tr>
        <tr class="row-3"><td>Average Employee<br>Growth</td><td>213%</td><td>49%</td></tr>
      </tbody>
    </table>
    <div class="bottom-bar">18</div><div class="bottom-accent"></div>
    <div class="footer-brand"><span class="dot"></span><span class="name">PINEBROOK<span class="tag">NON-CONTROL GROWTH CAPITAL</span></span></div>
  </section>

  <section class="slide">
    <div class="top-bar"></div>
    <h2 class="slide-title" style="top:60px">In Summary</h2>
    <ul class="bullets" style="left:12px;right:8px;top:98px">
      <li style="margin-bottom:12px">There is an alternative to giving up control of your company through an infusion of Non-Control Capital</li>
      <li style="margin-bottom:12px">All investors are not created equal</li>
      <li style="margin-bottom:8px">Non-Control Capital investing is a specialty:<span class="sub">- Choose only an investor with decades of Non-Control heritage, experience, and focus (see Questionnaire in the Epilogue section of this presentation)</span></li>
      <li style="margin-bottom:8px">It means more than just capital:<span class="sub">- Team up with an accomplished investor who can bring demonstrated growth abilities, not simply write a check</span></li>
      <li>Chemistry between company management and the investor is critical:<span class="sub">- If Pinebrook's interests are not aligned with management, we don't invest</span></li>
    </ul>
    <div class="bottom-bar">19</div><div class="bottom-accent"></div>
    <div class="footer-brand"><span class="dot"></span><span class="name">PINEBROOK<span class="tag">NON-CONTROL GROWTH CAPITAL</span></span></div>
  </section>

  <section class="slide slide--section"><h2 class="section-title">Epilogue</h2></section>

</main>
</body>
</html>
```